Lotstallmart.com Webpage Design

Design Brief for lotstallmart.com (Copy of Brief also in attached Word file)

Name of Website- lotstallmart.com (existing logo and look & feel of website to be changed)

Logo - Finalised. The logo files are attached with the brief as “logo.jpeg”. The “Blue- Grey” version of the logo is for use on lighter backgrounds and the “Orange-White” version of the logo is for use on darker backgrounds. (A full Black version of the logo is also attached). Both versions may be used in different parts of the website. All attached files are in .png format.
Status - The website in functional and is undergoing user trials. However, we want to improve the look & feel of the website so at it seems
a. cotemporary,
b. Easy to Navigate
c. professional and
d. Vibrant.

Please visit ‘lotstallmart.com’ to check out the website and its functionalities – please use it only as a reference for the features & functions to be provided, however the designer should use a ‘Free Hand’ in designing the composition of various parts of the webpage without getting too influenced by the existing design

Objective of the Website ‘lotstallmart.com –
a. It is a portal focussed on listing of ‘Retail’ specific real-estate properties by developers, owners and realty brokers. The properties shall listed under the following four categories-
i. Retail Malls
ii. Shopping Complexes
iii. High-street shops
iv. Retail Warehouses
*refer lotstallmart.com for better clarity

b. The abovementioned properties shall be listed either for ‘Sale’ or ‘rent\lease’ or both

c. Users shall visit the site in case they wish to acquire a retail \ shop space either on ‘sale’ or ‘rent’. These Users would be able to specify the ‘Search Criteria’ through the tool-bars provided on the website – the ‘Search Criteria’ shall comprise of ‘Type of space category’, ‘City’, ‘Locality’, transaction type ie ‘Rent \ Sale’ and ‘Area Range’

d. The main revenue model for the website shall be listing fee ( or advertising charges ) payable by those listing their properties on the website.

Three Main Pages of Website (lotstallmart.com) that need to be designed -
a. Main Home Page (visit the web link - http://lotstallmart.com/ ) - The main home page has the “Search Toolbar” for specifying of Search Criteria by the User. It shall also have the following features & functions-
i. Main Advertising Banner
ii. Featured Projects
iii. New Launches
iv. Toolbar with buttons – ‘Advertise with Us’, ‘Listings Alert’, ‘Mart Wizards’, ‘Advertiser Login’

b. Property Listings Page (visit the web link - http://lotstallmart.com/gurgaon-in-india ) - The List of property options that match the Criteria specified by the ‘User’ get displayed on this page.

c. Property Detail Page - When the ‘User’ clicks on the “More….” Button on the ‘Property Listings Page’ (given in point b. above) the web page with the details of the property opens. (For Example – visit the web link - http://lotstallmart.com/vorne-Shopping-Complex-vorne-quadrion-gurgaon-636 )

Note:- Please refer to attached ‘Shopping’ related images the designer may use them on the website to provide a look & feel of retail if required – either separately or rotate in a single window

Target Market(s)

Retailers & Investors looking for retail space, Real Estate Brokers, Developers

Industry/Entity Type

Advertising

Number of Pages Required

3 page

Requirements
Must have
• Refer to existing site lotstallmart.com -- all the existing functionalities are a must have.
Nice to have
• The Designer may use the retail related images on the website if required for making it more vibrant. Refer attached images Shopping(1-6).jpg

```html
<!DOCTYPE html>
<html lang="en">
<head>
<meta charset="utf-8">
<title>Lotstallmart.com – India's Leading Portal for Retail Space</title>
<link rel="stylesheet" href="https://fonts.googleapis.com/css2?family=Open+Sans:wght@300;400;600;700&display=swap">
<style>
:root{
  --blue:#1a9cec;
  --blue-dark:#1487d0;
  --ink:#333;
  --muted:#888;
  --light:#f2f2f2;
  --line:#dedede;
  --bar:#585858;
  --panel:rgba(20,20,20,.86);
  --foot:#2f2f2f;
  --foot-deep:#1f1f1f;
  --gold:#f5c518;
  --white:#fff;
}
*{box-sizing:border-box;margin:0;padding:0}
html,body{width:1200px;height:3041px;overflow:hidden}
body{font-family:"Open Sans",Arial,sans-serif;color:var(--ink);background:var(--white);position:relative}
a{color:inherit;text-decoration:none}

.city-bar{height:34px;background:var(--light);border-bottom:1px solid var(--line);display:flex;justify-content:center;align-items:center;gap:0;font-size:11.5px;color:#555}
.city-bar a{padding:0 11px;border-right:1px solid #c9c9c9;line-height:12px}
.city-bar a:last-child{border-right:0}

.site-header{height:140px;position:relative}
.brand{position:absolute;left:122px;top:74px;display:flex;align-items:center;gap:10px}
.brand-mark{width:40px;height:40px;border-radius:50%;background:var(--blue)}
.brand-name{font-size:34px;font-weight:600;color:var(--blue-dark);line-height:1}
.brand-tag{position:absolute;left:176px;top:118px;font-size:9px;font-weight:700;color:#555;letter-spacing:.3px}
.main-nav{position:absolute;left:507px;top:84px;display:flex;align-items:flex-start}
.main-nav a{display:block;text-align:center;padding:4px 16px;border-right:1px solid var(--line)}
.main-nav a:last-child{border-right:0}
.main-nav .nav-title{display:block;font-size:16px;color:var(--blue);text-transform:uppercase;line-height:20px}
.main-nav .nav-sub{display:block;font-size:10px;color:#999;line-height:14px}
.main-nav .current{border:1px solid #bbb;padding:4px 14px}

.advertiser-bar{height:51px;background:var(--blue);color:var(--white);display:flex;justify-content:center;align-items:center;font-size:12.5px;gap:14px}
.advertiser-bar strong{font-size:14px;font-weight:600}
.advertiser-bar .sep{opacity:.7}

.login-bar{height:95px;background:var(--bar);position:relative;font-size:12.5px;color:var(--white)}
.login-bar .field{position:absolute;top:28px;height:37px;width:215px;background:var(--white);color:#999;padding:0 12px;line-height:37px;font-size:13px}
.btn-blue{background:var(--blue);color:var(--white);font-weight:600;text-align:center}
.login-bar .sign-in{position:absolute;left:594px;top:28px;width:73px;height:37px;line-height:37px;font-size:14px}
.login-bar .keep{position:absolute;left:693px;top:38px;display:flex;align-items:center;gap:8px}
.box{width:13px;height:13px;background:var(--white);border:1px solid #ccc;display:inline-block}
.login-bar .forgot{position:absolute;left:837px;top:38px}
.login-bar .newadv{position:absolute;left:963px;top:20px;font-size:12px}
.login-bar .register{position:absolute;left:963px;top:42px;width:95px;height:24px;line-height:24px;background:#ddd;color:#444;font-size:11px;text-align:center;font-weight:600}

.hero{height:568px;position:relative;background:linear-gradient(100deg,#6b4b2a 0%,#b88a3c 30%,#d8b45a 45%,#c7a56e 60%,#7b8a98 80%,#aab3b8 100%)}
.hero-photo{position:absolute;inset:0}
.hero-arrow{position:absolute;top:266px;width:30px;height:30px;background:rgba(0,0,0,.55)}
.hero-arrow.left{left:0}.hero-arrow.right{right:0}
.search-panel{position:absolute;left:118px;top:14px;width:310px;height:554px;background:var(--panel);color:var(--white);padding:16px 22px}
.search-panel h2{font-size:25px;font-weight:400;line-height:32px}
.search-panel .meaning{color:var(--gold);font-size:15px;line-height:20px}
.formats{display:grid;grid-template-columns:136px 1fr;gap:10px 0;margin-top:18px;font-size:11.5px}
.formats span{display:flex;align-items:center;gap:8px}
.search-panel hr{border:0;border-top:1px solid #555;margin:18px -22px 14px}
.search-panel label{display:block;font-size:12.5px;margin-bottom:8px}
.select{height:38px;background:var(--white);color:#444;font-size:12.5px;line-height:38px;padding:0 12px;position:relative;margin-bottom:26px}
.select::after{content:"";position:absolute;right:14px;top:16px;border:6px solid transparent;border-top:7px solid #333}
.keyword{height:38px;background:var(--white);color:#999;font-size:12.5px;line-height:38px;padding:0 12px;position:relative}
.search-btn{display:block;width:80px;height:34px;line-height:34px;margin:14px 0 0 auto;font-size:14px;font-weight:400}

.categories{position:absolute;left:0;top:922px;width:1200px;height:50px}
.cat{position:absolute;top:0;display:flex;gap:8px}
.cat svg{margin-top:2px}
.cat b{display:block;font-size:18px;font-weight:600;color:var(--blue);line-height:22px}
.cat small{display:block;font-size:11.5px;color:#777;margin-left:14px}
.divider{position:absolute;left:118px;top:985px;width:962px;border-top:1px solid var(--line)}

.listing{position:absolute;left:118px;width:962px;background:var(--light);padding:0 10px}
.listing h2{font-size:24px;font-weight:600;color:var(--blue);text-transform:uppercase;height:70px;line-height:78px;padding-left:4px}
.listing .pin{position:absolute;right:16px;top:16px}
.grid{display:grid;grid-template-columns:repeat(5,178px);gap:20px 13px}
.card{background:var(--white);border:1px solid var(--line);height:217px;padding:9px;text-align:center}
.card .thumb{height:112px;margin-bottom:12px}
.card .name{font-size:13px;color:#333;line-height:20px}
.card .city{font-size:13px;color:var(--blue);line-height:22px}
.card .type{font-size:11.5px;color:#888;line-height:20px}
.featured{top:989px;height:556px}
.launches{top:2057px;height:550px}

.wizards{position:absolute;left:118px;top:1565px;width:962px;height:462px}
.wizards-form{position:absolute;left:0;top:0;width:480px;height:462px;background:var(--blue);color:var(--white);padding:42px 52px}
.wizards-form h2{font-size:29px;font-weight:600;line-height:36px}
.wizards-form p{font-size:13px;line-height:22px;margin:4px 0 14px;width:390px}
.wizards-form .input{width:260px;height:35px;background:var(--white);color:#777;font-size:12.5px;padding:0 12px;line-height:35px;margin-bottom:14px}
.wizards-form .textarea{height:104px;line-height:22px;padding-top:8px;margin-bottom:0}
.wizards-form .submit{position:absolute;left:328px;top:381px;width:78px;height:34px;line-height:34px;background:#333;color:var(--white);font-size:13px;text-align:center;font-weight:600}
.wizards-photo{position:absolute;left:480px;top:30px;width:482px;height:432px;background:linear-gradient(120deg,#f0f0f0 0%,#d7cfc6 30%,#8c6a5a 55%,#c9b9aa 75%,#eeeeee 100%)}

.alert-bar{position:absolute;left:0;top:2635px;width:1200px;height:79px;background:var(--blue);display:flex;align-items:center;padding-left:120px;gap:10px}
.alert-bar h2{font-size:30px;font-weight:300;color:var(--white);width:210px}
.alert-bar .field{width:207px;height:35px;background:var(--white);color:#444;font-size:13px;line-height:35px;padding:0 14px;position:relative}
.alert-bar .field.drop::after{content:"";position:absolute;right:12px;top:15px;border:5px solid transparent;border-top:6px solid #777}
.alert-bar .subscribe{height:35px;line-height:35px;padding:0 14px;background:#222;color:var(--white);font-size:14px}

.site-footer{position:absolute;left:0;top:2714px;width:1200px;height:252px;background:linear-gradient(#3a3a3a,#282828);color:#ccc}
.foot-col{position:absolute;top:32px;font-size:12px;line-height:24px}
.foot-col h3{font-size:14px;font-weight:600;color:var(--white);margin-bottom:8px;line-height:20px}
.foot-col ul{list-style:none}
.foot-col li::before{content:"• "}
.foot-col p{color:#999;font-size:12px;line-height:22px}
.foot-col .more{display:block;color:var(--white);font-weight:700;font-size:12px;margin-top:4px}
.foot-col.split{border-left:1px solid #555;padding-left:22px;height:200px}
.foot-brand{position:absolute;left:872px;top:52px;display:flex;align-items:center;gap:8px}
.foot-brand .brand-mark{width:30px;height:30px;background:#f39a1e}
.foot-brand span{font-size:26px;font-weight:600;color:var(--white)}
.copyright{position:absolute;left:0;top:2966px;width:1200px;height:75px;background:var(--foot-deep);color:#aaa;font-size:12px;line-height:75px;padding-left:122px}
.social{position:absolute;right:122px;top:20px;display:flex;gap:10px}
.social span{width:32px;height:32px;border-radius:50%}
</style>
</head>
<body>

<nav class="city-bar">
  <a href="#">Bangalore</a><a href="#">Chennai</a><a href="#">Greater Noida</a><a href="#">Gurgaon</a><a href="#">Hyderabad</a><a href="#">Jaipur</a><a href="#">Khanna</a><a href="#">Kolkatta</a><a href="#">Mumbai</a><a href="#">Noida</a><a href="#">Pune</a><a href="#">Surat</a><a href="#">More</a>
</nav>

<header class="site-header">
  <a class="brand" href="http://lotstallmart.com/"><span class="brand-mark"></span><span class="brand-name">lotstallmart</span></a>
  <span class="brand-tag">INDIA'S LEADING PORTAL FOR RETAIL SPACE</span>
  <nav class="main-nav">
    <a href="#" class="current"><span class="nav-title">Home</span><span class="nav-sub">Welcome</span></a>
    <a href="#"><span class="nav-title">Advertise with us</span><span class="nav-sub">Standard listing - FREE</span></a>
    <a href="#"><span class="nav-title">Mart Wizards</span><span class="nav-sub">Shop Search Services</span></a>
    <a href="#"><span class="nav-title">Listing Alert</span><span class="nav-sub">Newsletter Subscribe</span></a>
  </nav>
</header>

<div class="advertiser-bar">
  <span>List your Property Here</span><span class="sep">|</span>
  <strong>&#9679; ADVERTISER LOGIN</strong><span class="sep">|</span>
  <span>New Advertiser - Register</span>
</div>

<div class="login-bar">
  <div class="field" style="left:140px">Username</div>
  <div class="field" style="left:367px">Password</div>
  <div class="sign-in btn-blue">SIGN IN</div>
  <div class="keep"><span class="box"></span>Keep me logged in</div>
  <div class="forgot">Forgot Password</div>
  <div class="newadv">New Advertiser?</div>
  <div class="register">REGISTER</div>
</div>

<section class="hero">
  <div class="hero-photo" role="img" aria-label="Family out shopping in a retail store with sale signs"></div>
  <span class="hero-arrow left"><svg width="30" height="30"><path d="M18 9l-6 6 6 6" stroke="#fff" stroke-width="2.5" fill="none"/></svg></span>
  <span class="hero-arrow right"><svg width="30" height="30"><path d="M12 9l6 6-6 6" stroke="#fff" stroke-width="2.5" fill="none"/></svg></span>
  <form class="search-panel">
    <h2>Select Retail Format :</h2>
    <div class="meaning">Meaning of Retail Format</div>
    <div class="formats">
      <span><i class="box"></i>Retail Mall</span><span><i class="box"></i>Shopping Complex</span>
      <span><i class="box"></i>High Street Shops</span><span><i class="box"></i>Retail Warehouses</span>
    </div>
    <hr>
    <label>Sale Or Rent Or Both :</label><div class="select">Both</div>
    <label>Select City :</label><div class="select">Select</div>
    <label>Select Locality/Micro-Market.</label><div class="select">Select</div>
    <label>Enter Keyword :</label>
    <div class="keyword">Name of Project or Developer etc
      <svg style="position:absolute;right:10px;top:10px" width="18" height="18"><circle cx="7" cy="7" r="5.5" stroke="#333" stroke-width="2" fill="none"/><path d="M11 11l5 5" stroke="#333" stroke-width="2.4"/></svg>
    </div>
    <div class="search-btn btn-blue">SEARCH</div>
  </form>
</section>

<div class="categories">
  <div class="cat" style="left:122px"><svg width="22" height="22"><circle cx="11" cy="11" r="11" fill="#1a9cec"/><path d="M6 11l4 4 6-7" stroke="#fff" stroke-width="2.4" fill="none"/></svg><div><b>RETAIL MALLS</b><small>Centrally Air-Conditioned</small></div></div>
  <div class="cat" style="left:341px"><svg width="22" height="22"><circle cx="11" cy="11" r="11" fill="#1a9cec"/><path d="M6 11l4 4 6-7" stroke="#fff" stroke-width="2.4" fill="none"/></svg><div><b>SHOPPING COMPLEX</b><small>Non Air-Conditioned Building</small></div></div>
  <div class="cat" style="left:602px"><svg width="22" height="22"><circle cx="11" cy="11" r="11" fill="#1a9cec"/><path d="M6 11l4 4 6-7" stroke="#fff" stroke-width="2.4" fill="none"/></svg><div><b>HIGH STREET SHOPS</b><small>Road Facing Retail</small></div></div>
  <div class="cat" style="left:860px"><svg width="22" height="22"><circle cx="11" cy="11" r="11" fill="#1a9cec"/><path d="M6 11l4 4 6-7" stroke="#fff" stroke-width="2.4" fill="none"/></svg><div><b>RETAIL WAREHOUSES</b><small>Back-end Retail Storage</small></div></div>
</div>
<div class="divider"></div>

<section class="listing featured">
  <h2>Featured Projects</h2>
  <svg class="pin" width="34" height="34"><circle cx="15" cy="12" r="8" stroke="#1a9cec" stroke-width="3" fill="none"/><path d="M20 18l9 9" stroke="#1a9cec" stroke-width="3.5"/><path d="M2 31h28" stroke="#1a9cec" stroke-width="2"/></svg>
  <div class="grid">
    <div class="card"><div class="thumb" role="img" aria-label="Mall building exterior" style="background:linear-gradient(#bcd3e6,#8a8f86)"></div><div class="name">Corvin Arcade</div><div class="city">SURAT</div><div class="type">Shopping Complex</div></div>
    <div class="card"><div class="thumb" role="img" aria-label="Lit complex at dusk" style="background:linear-gradient(#3a5070,#7b6a52)"></div><div class="name">Corvin Arcade</div><div class="city">SURAT</div><div class="type">Shopping Complex</div></div>
    <div class="card"><div class="thumb" role="img" aria-label="Glass retail building" style="background:linear-gradient(#9fc2dc,#5f8a8a)"></div><div class="name">Corvin Arcade</div><div class="city">SURAT</div><div class="type">Shopping Complex</div></div>
    <div class="card"><div class="thumb" role="img" aria-label="Tower complex rendering" style="background:linear-gradient(#2f5c96,#b48a4c)"></div><div class="name">Corvin Arcade</div><div class="city">SURAT</div><div class="type">Shopping Complex</div></div>
    <div class="card"><div class="thumb" role="img" aria-label="Modern mall facade" style="background:linear-gradient(#7fa4c6,#6b6b70)"></div><div class="name">Corvin Arcade</div><div class="city">SURAT</div><div class="type">Shopping Complex</div></div>
    <div class="card"><div class="thumb" role="img" aria-label="Storefront with awning" style="background:linear-gradient(#e3e3e3,#b0553c)"></div><div class="name">Corvin Arcade</div><div class="city">SURAT</div><div class="type">Shopping Complex</div></div>
    <div class="card"><div class="thumb" role="img" aria-label="Red and white complex" style="background:linear-gradient(#5f7ea6,#a4433a)"></div><div class="name">Corvin Arcade</div><div class="city">SURAT</div><div class="type">Shopping Complex</div></div>
    <div class="card"><div class="thumb" role="img" aria-label="Gallery mall building" style="background:linear-gradient(#c8d8e8,#8a96a4)"></div><div class="name">Corvin Arcade</div><div class="city">SURAT</div><div class="type">Shopping Complex</div></div>
    <div class="card"><div class="thumb" role="img" aria-label="Blue glass tower" style="background:linear-gradient(#2a66a8,#6ea0cf)"></div><div class="name">Corvin Arcade</div><div class="city">SURAT</div><div class="type">Shopping Complex</div></div>
    <div class="card"><div class="thumb" role="img" aria-label="Tower complex rendering" style="background:linear-gradient(#2f5c96,#b48a4c)"></div><div class="name">Corvin Arcade</div><div class="city">SURAT</div><div class="type">Shopping Complex</div></div>
  </div>
</section>

<section class="wizards">
  <form class="wizards-form">
    <h2>MART WIZARDS</h2>
    <p>Post your Retail Space requirement with us and our experts shall get back with suitable options and even help yotu in your transaction. This is a Free Service!</p>
    <div class="input">Enter your name</div>
    <div class="input">Enter your email address</div>
    <div class="input">Mobile</div>
    <div class="input textarea">Add Description of Requirement</div>
    <div class="submit">SUBMIT</div>
  </form>
  <div class="wizards-photo" role="img" aria-label="Three women walking with shopping bags"></div>
</section>

<section class="listing launches">
  <h2>New Launches</h2>
  <svg class="pin" width="34" height="34"><circle cx="15" cy="12" r="8" stroke="#1a9cec" stroke-width="3" fill="none"/><path d="M20 18l9 9" stroke="#1a9cec" stroke-width="3.5"/><path d="M2 31h28" stroke="#1a9cec" stroke-width="2"/></svg>
  <div class="grid">
    <div class="card"><div class="thumb" role="img" aria-label="Mall with colourful facade" style="background:linear-gradient(#e6e0e6,#9b6a8c)"></div><div class="name">Corvin Arcade</div><div class="city">SURAT</div><div class="type">Shopping Complex</div></div>
    <div class="card"><div class="thumb" role="img" aria-label="Complex at night" style="background:linear-gradient(#1f3e6e,#8a6a40)"></div><div class="name">Corvin Arcade</div><div class="city">SURAT</div><div class="type">Shopping Complex</div></div>
    <div class="card"><div class="thumb" role="img" aria-label="Low rise shopping block" style="background:linear-gradient(#a9c4dc,#8c7a68)"></div><div class="name">Corvin Arcade</div><div class="city">SURAT</div><div class="type">Shopping Complex</div></div>
    <div class="card"><div class="thumb" role="img" aria-label="Pink retail building" style="background:linear-gradient(#c9d6e4,#b48a8c)"></div><div class="name">Corvin Arcade</div><div class="city">SURAT</div><div class="type">Shopping Complex</div></div>
    <div class="card"><div class="thumb" role="img" aria-label="Glass mall facade" style="background:linear-gradient(#4a78a8,#8ca0b4)"></div><div class="name">Corvin Arcade</div><div class="city">SURAT</div><div class="type">Shopping Complex</div></div>
    <div class="card"><div class="thumb" role="img" aria-label="White mall with blue glass" style="background:linear-gradient(#8cb4dc,#dadada)"></div><div class="name">Corvin Arcade</div><div class="city">SURAT</div><div class="type">Shopping Complex</div></div>
    <div class="card"><div class="thumb" role="img" aria-label="Curved office and retail block" style="background:linear-gradient(#5a9ad0,#e4e8ec)"></div><div class="name">Corvin Arcade</div><div class="city">SURAT</div><div class="type">Shopping Complex</div></div>
    <div class="card"><div class="thumb" role="img" aria-label="Lit tower at night" style="background:linear-gradient(#241a2a,#8a4a2a)"></div><div class="name">Corvin Arcade</div><div class="city">SURAT</div><div class="type">Shopping Complex</div></div>
    <div class="card"><div class="thumb" role="img" aria-label="Mall at dusk" style="background:linear-gradient(#3c5a8c,#a48c7a)"></div><div class="name">Corvin Arcade</div><div class="city">SURAT</div><div class="type">Shopping Complex</div></div>
    <div class="card"><div class="thumb" role="img" aria-label="Mall interior" style="background:linear-gradient(#b0b4b8,#5a5e62)"></div><div class="name">Corvin Arcade</div><div class="city">SURAT</div><div class="type">Shopping Complex</div></div>
  </div>
</section>

<form class="alert-bar">
  <h2>LISTING ALERT</h2>
  <div class="field">Email ID</div>
  <div class="field drop">Select Option</div>
  <div class="field drop">Adilabad</div>
  <div class="subscribe">Subscribe</div>
</form>

<footer class="site-footer">
  <div class="foot-col" style="left:118px;width:250px">
    <h3>About Stall Central</h3>
    <ul style="float:left;width:115px"><li>About Us</li><li>Privacy Policy</li><li>Terms of Use</li><li>Contact Us</li><li>Site Map</li></ul>
    <ul style="float:left"><li>Retail Malls</li><li>Shopping Complex</li><li>High Street Shops</li><li>Retail Warehouses</li></ul>
  </div>
  <div class="foot-col split" style="left:368px;width:232px">
    <h3>About us</h3>
    <p>Our team maps retail space across India and keeps each listing current. We visit sites, check papers and talk to owners so that buyers and tenants can compare options with care and act with confidence.</p>
    <span class="more">MORE</span>
  </div>
  <div class="foot-col split" style="left:600px;width:252px">
    <h3>Editor's Choice</h3>
    <p>A "Select" Listing of Retail Properties Handpicked by our Editors based on their own positive evaluation on parameters &amp; attributes such as Design Concept, Location, Developer, Success Potential. So Read On to Check Out for yourself ........</p>
    <span class="more">MORE</span>
  </div>
  <div class="foot-col split" style="left:852px;width:4px;padding:0"></div>
  <div class="foot-brand"><span class="brand-mark"></span><span>lotstallmart</span></div>
</footer>

<div class="copyright">
  Copyright © 2014 Lotstallmart.com. &nbsp;All rights reserved.
  <div class="social">
    <span style="background:#3b5998"></span><span style="background:#29a9e0"></span><span style="background:#d8473a"></span><span style="background:#c8302a"></span><span style="background:#1a7bb9"></span><span style="background:#4caf50"></span>
  </div>
</div>

</body>
</html>
```